I need a logo that demonstrates multiple of the same with one of a distinguishing feature. I would like something that can be recognisable in silhouette format. The business designs Management systems bespoke the to the company helping them pre-qualify for work.
Something that can demonstrate a distinction between a collective group non of which are the same in shape or size, with the largest of these not the distinguished object (or something to that effect).
This is a new business no logo or artwork exists.
Target Market(s)
Small to Medium Size enterprises in the city and rural areas. Looking to make the step up.
Industry/Entity Type
Manufacture
Contact Information for Business Card
room for, Name, Email, phone number
Font styles to use
Requirements
Must have
- would like the silhouette to be recognisable
Nice to have
- would like it to incorporate the name Keystone Advisory Frameworks.
- Would like the same logo to be on both business cards and on corporate shirts
Should not have
- anything that may exclude rural trade or manufacturing.
- I don't want to appear as corporate, just professional

```html
<!DOCTYPE html>
<html lang="en">
<head>
<meta charset="utf-8">
<title>Keystone Advisory Frameworks – Business Card</title>
<link rel="stylesheet" href="https://fonts.googleapis.com/css2?family=Questrial&family=Open+Sans:wght@400;600;700&display=swap">
<style>
  :root {
    --canvas: #ecebe8;
    --card-white: #ffffff;
    --card-black: #0d0d0d;
    --brand-red: #e3202a;
    --brand-grey: #9b9b9b;
    --ink: #2a2a2a;
    --ink-soft: #555555;
  }
  * { box-sizing: border-box; margin: 0; padding: 0; }
  html, body { width: 1200px; height: 900px; overflow: hidden; }
  body {
    background: var(--canvas);
    font-family: "Open Sans", Arial, sans-serif;
    position: relative;
  }
  .card {
    position: absolute;
    left: 300px;
    width: 600px;
    height: 343px;
    overflow: hidden;
    box-shadow: 0 6px 18px rgba(0,0,0,0.18);
  }
  .card--back {
    top: 70px;
    background:
      repeating-linear-gradient(0deg, rgba(255,255,255,0.025) 0 1px, transparent 1px 3px),
      linear-gradient(120deg, #050505 0%, #1c1c1c 55%, #080808 100%);
    display: flex;
    align-items: center;
    justify-content: center;
  }
  .card--front {
    top: 487px;
    background: var(--card-white);
  }
  .wordmark {
    font-family: "Questrial", "Century Gothic", sans-serif;
    font-weight: 400;
    line-height: 1;
  }
  .wordmark__main { display: block; letter-spacing: 2px; }
  .wordmark__sub { display: block; }
  .card--back .wordmark { color: #ffffff; }
  .card--back .wordmark__main { font-size: 58px; }
  .card--back .wordmark__sub { font-size: 29px; margin-top: 4px; }

  .front-decor { position: absolute; inset: 0; }
  .holder {
    position: absolute;
    left: 68px;
    top: 24px;
  }
  .holder__name {
    font-size: 19px;
    font-weight: 700;
    color: var(--brand-grey);
    line-height: 1.1;
  }
  .holder__name .surname { color: var(--brand-red); }
  .holder__role {
    font-size: 12.5px;
    color: var(--ink);
  }
  .contact {
    position: absolute;
    left: 36px;
    top: 128px;
    font-size: 13.5px;
    color: var(--ink);
    line-height: 1.3;
    list-style: none;
  }
  .contact__address { margin-bottom: 12px; }
  .contact__line { display: flex; align-items: center; gap: 7px; }
  .contact__icon { width: 11px; height: 11px; fill: var(--brand-red); flex: none; }

  .card--front .logo {
    position: absolute;
    left: 306px;
    top: 140px;
    display: flex;
    align-items: center;
    gap: 10px;
    color: var(--brand-red);
  }
  .logo__dot {
    width: 16px; height: 16px; border-radius: 50%;
    background: var(--brand-red); flex: none;
  }
  .card--front .wordmark__main { font-size: 38px; }
  .card--front .wordmark__sub { font-size: 19.5px; margin-top: 3px; }
</style>
</head>
<body>

<section class="card card--back" aria-label="Business card, back">
  <h1 class="wordmark">
    <span class="wordmark__main">KEYSTONE</span>
    <span class="wordmark__sub">Advisory Frameworks</span>
  </h1>
</section>

<section class="card card--front" aria-label="Business card, front">
  <svg class="front-decor" width="600" height="343" viewBox="0 0 600 343" aria-hidden="true">
    <polygon points="0,22 22,22 0,48" fill="var(--brand-grey)"/>
    <polygon points="30,22 58,22 44,52 14,52" fill="var(--brand-red)"/>
    <polygon points="0,290 290,290 282,304 0,304" fill="var(--brand-grey)" opacity="0.55"/>
    <polygon points="300,290 600,290 600,343 275,343" fill="var(--brand-red)"/>
  </svg>

  <div class="holder">
    <p class="holder__name">Daniel <span class="surname">Hart</span></p>
    <p class="holder__role">Managing Director</p>
  </div>

  <ul class="contact">
    <li class="contact__address">48 Millbrook Lane<br>Northfield, NF4 2KA</li>
    <li class="contact__line">
      <svg class="contact__icon" viewBox="0 0 12 12"><path d="M2 1h3l1 3-2 1a7 7 0 0 0 3 3l1-2 3 1v3c0 1-1 1-1 1A10 10 0 0 1 1 2c0 0 0-1 1-1z"/></svg>
      044-987 654 321
    </li>
    <li class="contact__line">
      <svg class="contact__icon" viewBox="0 0 12 12"><path d="M3 1h6v3H3z M1 5h10v5H9V8H3v2H1z M4 9h4v2H4z"/></svg>
      044-987 654 321
    </li>
    <li class="contact__line">
      <svg class="contact__icon" viewBox="0 0 12 12"><path d="M1 2h10v8H1z" /><path d="M1 2l5 4 5-4" stroke="#fff" stroke-width="1.2" fill="none"/></svg>
      hello@keystoneaf.com
    </li>
  </ul>

  <div class="logo">
    <span class="logo__dot"></span>
    <p class="wordmark">
      <span class="wordmark__main">KEYSTONE</span>
      <span class="wordmark__sub">Advisory Frameworks</span>
    </p>
  </div>
</section>

</body>
</html>
```